Quiet Harbor, Weekly therapy lessons for the heart of a sister missionary

This is a weekly guided therapy book for female Mormon missionaries. They leave for their missions for 18 months and I am a psychotherapist that is creating a guided workbook to help them through mental health struggles on their mission. I need a good book cover, also preferably something for the spine and back as well. I would like something that gives a soft and safe feeling.

```html
<!DOCTYPE html>
<html lang="en">
<head>
<meta charset="UTF-8">
<title>Quiet Harbor – Book Cover</title>
<link rel="stylesheet" href="https://fonts.googleapis.com/css2?family=EB+Garamond:wght@400;500;600&display=swap">
<style>
  :root {
    --backdrop: #ece7df;
    --paper: #fdfcf7;
    --ink-gold: #857444;
    --ink-soft: #8f7f52;
    --blush: #dba89c;
    --blush-light: #ecc9bf;
    --sage: #a8bfae;
    --sage-deep: #8fab98;
  }
  * { margin: 0; padding: 0; box-sizing: border-box; }
  html, body {
    width: 1200px;
    height: 730px;
    overflow: hidden;
    background: var(--backdrop);
  }
  .stage {
    width: 1200px;
    height: 730px;
    display: flex;
    align-items: center;
    justify-content: center;
  }
  .book-cover {
    position: relative;
    width: 430px;
    height: 680px;
    background: var(--paper);
    box-shadow: 0 6px 24px rgba(80, 60, 30, 0.12);
    font-family: "EB Garamond", Georgia, serif;
    text-align: center;
  }
  .book-title {
    position: absolute;
    top: 52px;
    left: 0;
    right: 0;
    font-size: 58px;
    font-weight: 600;
    letter-spacing: -0.5px;
    color: var(--ink-gold);
    line-height: 1;
  }
  .book-subtitle {
    position: absolute;
    top: 138px;
    left: 0;
    right: 0;
    font-size: 19px;
    font-weight: 400;
    line-height: 1.22;
    color: var(--ink-soft);
  }
  .cover-artwork {
    position: absolute;
    top: 232px;
    left: 0;
    right: 0;
    height: 300px;
    background:
      linear-gradient(to bottom,
        rgba(253,252,247,1) 0%,
        rgba(253,252,247,0) 22%,
        rgba(253,252,247,0) 78%,
        rgba(253,252,247,1) 100%),
      linear-gradient(to bottom,
        var(--paper) 0%,
        var(--blush-light) 28%,
        var(--blush) 40%,
        var(--sage) 56%,
        var(--sage-deep) 66%,
        var(--blush) 80%,
        var(--blush-light) 90%,
        var(--paper) 100%);
  }
  .author-name {
    position: absolute;
    bottom: 62px;
    left: 0;
    right: 0;
    font-size: 25px;
    font-weight: 500;
    letter-spacing: 4px;
    color: var(--ink-soft);
  }
</style>
</head>
<body>
  <main class="stage">
    <article class="book-cover">
      <h1 class="book-title">Quiet Harbor</h1>
      <p class="book-subtitle">Weekly therapy lessons for<br>the heart of a sister missionary</p>
      <div class="cover-artwork" role="img" aria-label="Watercolour landscape of blush and sage hills with a rising golden sun, a gold line heart and a winding path"></div>
      <p class="author-name">AUTHOR NAME</p>
    </article>
  </main>
</body>
</html>
```